Brisk Harbor claims recovery services

Its a new company in Dubai UAE. The company activity is debt management, debt collection, loans settlements and restructuring. The company involved in any business or sector requires debt management including government entities, Medical & Health care sector, Banks & finance companies, SME's and commercial business.

Target Market(s)

government entities, Medical & Health care sector, Banks & finance companies, SME's and commercial business.

Industry/Entity Type

Financial Service

Number of Pages Required

5+ page

Requirements
Must have
• Focus on the services not the team and clients
Should not have
• Colorful . Shouldn't have Client testimonial and our clients

```html
<!DOCTYPE html>
<html lang="en">
<head>
<meta charset="utf-8">
<title>Brisk Harbor — Contact Us</title>
<link href="https://fonts.googleapis.com/css2?family=Open+Sans:wght@400;600;700&family=Cinzel:wght@400;600&family=Roboto:wght@400;500&display=swap" rel="stylesheet">
<style>
:root{
  --navy:#0d4a72;
  --blue:#155b8a;
  --text:#555;
  --muted:#888;
  --line:#d9d9d9;
  --band:#f5f5f5;
  --nav-top:#b3b3b3;
  --nav-bottom:#8f8f8f;
}
*{margin:0;padding:0;box-sizing:border-box}
html,body{width:769px;height:1200px;overflow:hidden;background:#fff}
body{font-family:"Open Sans",sans-serif;color:var(--text);position:relative}
.abs{position:absolute}

/* header */
.brand{left:63px;top:17px;display:flex;align-items:center;gap:8px}
.brand-box{width:34px;height:34px;background:var(--navy)}
.brand-name{font-family:"Cinzel",serif;font-size:19px;color:var(--navy);line-height:1;white-space:nowrap}
.brand-tag{font-family:"Cinzel",serif;font-size:4.6px;letter-spacing:2.2px;color:var(--muted);margin-top:4px;white-space:nowrap}
.call{left:429px;top:25px;display:flex;align-items:center;gap:6px;font-size:8px;color:var(--muted);white-space:nowrap}
.call b{color:var(--navy);font-size:9.5px}
.quote-btn{left:596px;top:24px;width:110px;height:27px;background:var(--navy);color:#fff;font-size:7px;font-weight:600;display:flex;align-items:center;justify-content:center;border-radius:2px}

/* nav */
.nav{left:0;top:72px;width:769px;height:34px;background:linear-gradient(var(--nav-top),var(--nav-bottom))}
.nav span{position:absolute;top:0;height:34px;line-height:34px;color:#fff;font-size:7px;text-align:center}
.nav .active{background:var(--navy)}

/* hero */
.hero{left:0;top:106px;width:769px;height:245px;background:linear-gradient(100deg,#0f2236 0%,#1d3550 40%,#22334a 60%,#2a2e35 80%,#1a1c20 100%)}
.hero-floor{left:0;top:260px;width:769px;height:91px;background:linear-gradient(#3b3226,#15120f)}
.hero-mark{left:63px;top:200px;width:47px;height:57px;border:3px solid #fff}
.hero-title{left:121px;top:203px;font-family:"Cinzel",serif;color:#fff;font-size:18.5px;font-weight:600;letter-spacing:.5px;white-space:nowrap}
.hero-sub{left:121px;top:235px;font-family:"Cinzel",serif;color:#fff;font-size:12.5px;letter-spacing:.8px;white-space:nowrap}

/* contact */
.h-contact{left:0;top:377px;width:769px;text-align:center;color:var(--navy);font-size:17px;font-weight:600}
.lead{left:176px;top:402px;width:417px;text-align:center;font-size:7.8px;line-height:15.4px;color:var(--muted)}
.map{left:63px;top:461px;width:344px;height:154px;background:linear-gradient(135deg,#f2efe2,#e7e5d8 60%,#dcdfe6)}
.info{left:434px;top:462px;width:272px;font-size:7px;color:#333}
.info-row{display:flex;align-items:center;gap:5px;height:13px;white-space:nowrap}
.info p{margin-top:9px;color:var(--muted);font-size:6.9px;line-height:15.3px}

/* signup */
.signup{left:0;top:648px;width:769px;height:372px;background:var(--band)}
.h-signup{left:0;top:680px;width:769px;text-align:center;color:var(--navy);font-size:10.5px;font-weight:600}
.signup-lead{left:0;top:703px;width:769px;text-align:center;font-size:7.8px;color:var(--muted);white-space:nowrap}
.field{background:#fff;border:1px solid var(--line);font-size:6.8px;color:var(--muted);padding:9px 0 0 10px}
.submit{left:358px;top:870px;width:53px;height:20px;background:var(--navy);color:#fff;font-size:6.5px;font-weight:700;display:flex;align-items:center;justify-content:center;border-radius:2px}

/* footer */
.footer{left:0;top:1020px;width:769px;height:180px;background:var(--navy)}
.f-brand{left:63px;top:1047px;display:flex;align-items:center;gap:6px;color:#fff}
.f-brand .brand-box{width:22px;height:22px;background:#fff}
.f-brand .brand-name{color:#fff;font-size:12px}
.f-brand .brand-tag{color:#b8c7d4;font-size:3.4px;letter-spacing:1.6px;margin-top:2px}
.f-text{color:#fff;font-size:7px;line-height:15px}
.f-head{font-family:"Roboto",sans-serif;color:#fff;font-size:10px;font-weight:500}
.f-links{font-size:7px;color:#fff;line-height:17px}
.nl-input{left:377px;top:1113px;width:108px;height:24px;background:var(--blue);color:#b8cbda;font-size:6.6px;padding:8px 0 0 9px;white-space:nowrap}
.nl-btn{left:485px;top:1113px;width:51px;height:24px;background:#fff;color:var(--navy);font-family:"Roboto",sans-serif;font-size:9.5px;display:flex;align-items:center;justify-content:center}
.social{top:1173px;width:18px;height:18px;border-radius:50%;background:#fff}
</style>
</head>
<body>

<!-- header -->
<div class="abs brand">
  <div class="brand-box"></div>
  <div><div class="brand-name">BRISK HARBOR</div><div class="brand-tag">CLAIMS RECOVERY SERVICES</div></div>
</div>
<div class="abs call">
  <svg width="24" height="24" viewBox="0 0 24 24"><circle cx="12" cy="12" r="11" fill="none" stroke="#0d4a72" stroke-width="1.2"/><path d="M9 7.5l2 2.2-1.2 1.3c.6 1.4 1.7 2.5 3.1 3.1l1.3-1.2 2.2 2-1.3 1.6c-3.6-.4-6.6-3.4-7-7z" fill="#0d4a72"/></svg>
  Call Us Today : <b>(+111) 555-0142</b>
</div>
<div class="abs quote-btn">REQUEST A QUOTE</div>

<nav class="abs nav">
  <span style="left:90px;width:60px">HOME</span>
  <span style="left:235px;width:60px">ABOUT US</span>
  <span style="left:390px;width:60px">SERVICES</span>
  <span class="active" style="left:618px;width:87px">CONTACT US</span>
</nav>

<!-- hero -->
<div class="abs hero" role="img" aria-label="Photograph of a businessman's hand stopping a row of falling wooden dominoes"></div>
<div class="abs hero-floor" role="img" aria-label="Wooden dominoes on a reflective desk"></div>
<svg class="abs" style="left:36px;top:212px" width="12" height="32" viewBox="0 0 12 32"><path d="M10 1L2 16l8 15" fill="none" stroke="#8a97a6" stroke-width="1"/></svg>
<svg class="abs" style="left:721px;top:212px" width="12" height="32" viewBox="0 0 12 32"><path d="M2 1l8 15-8 15" fill="none" stroke="#8a97a6" stroke-width="1"/></svg>
<div class="abs hero-mark"></div>
<div class="abs hero-title">MANAGING YOUR MONEY</div>
<div class="abs hero-sub">RECOVERING YOUR RELATIONSHIPS</div>

<!-- contact -->
<h1 class="abs h-contact">CONTACT US</h1>
<p class="abs lead">Intelligent lending opens doors and allows ambitious individuals and fledgling businesses to grow. But without careful planning and management, debt can become overwhelming.</p>
<div class="abs map" role="img" aria-label="Street map showing the office location with a red pin"></div>
<svg class="abs" style="left:268px;top:512px" width="22" height="33" viewBox="0 0 22 33"><path d="M11 1C5.5 1 1 5.3 1 10.8 1 18 11 32 11 32s10-14 10-21.2C21 5.3 16.5 1 11 1z" fill="#e53935"/><circle cx="11" cy="10.5" r="4" fill="#fff"/></svg>

<div class="abs info">
  <div class="info-row">
    <svg width="8" height="8" viewBox="0 0 10 10"><path d="M9.5.5L.5 4.5 4.5 5.5 5.5 9.5z" fill="#0d4a72"/></svg>
    410 BRISK HARBOR, MARINA WALK, DUBAI-00000
  </div>
  <div class="info-row" style="margin-top:8px">
    <svg width="8" height="8" viewBox="0 0 10 10"><path d="M1 1.5l2.4-.5 1.1 2.4-1.2 1c.6 1.2 1.4 2 2.5 2.5l1-1.2 2.4 1.1-.5 2.4C4.6 9.2.8 5.4 1 1.5z" fill="#0d4a72"/></svg>
    +111-555-0142
    <svg style="margin-left:20px" width="9" height="7" viewBox="0 0 9 7"><rect width="9" height="7" fill="#0d4a72"/><path d="M0 0l4.5 3.5L9 0" fill="none" stroke="#fff" stroke-width=".8"/></svg>
    hello@briskharbor.example
  </div>
  <p>Accusamus et iusto odio dignissimos ducimus qui blanditiis praesentium ipsums voluptatum cupiditate non provident, similique sunt in culpa qui officia deserunt mollitia animi, id est laborum et dolorum fuga. Et harum quidem rerum facilis est et expedita distinctio. Nam libero tempore, cum soluta nobis est eligendi optioer cumque nihil impedit quo minus id quod maxime placeat facere possimuserdas, molestiae non recusandae. Itaque earum rerum hic tenetur a sapiente delectus, ut aut reiciendis voluptatibus maiores alias consequatur...</p>
</div>

<!-- signup -->
<section class="abs signup"></section>
<h2 class="abs h-signup">EMAIL SIGNUP</h2>
<p class="abs signup-lead">Your time is precious. Will you spend thirty minutes of it with us?We'dlove to hear about your plans and dreams, and maybe see if we could be a good fit.</p>
<div class="abs field" style="left:221px;top:734px;width:155px;height:24px">First name</div>
<div class="abs field" style="left:385px;top:734px;width:155px;height:24px">Last name</div>
<div class="abs field" style="left:221px;top:769px;width:155px;height:24px">Email</div>
<div class="abs field" style="left:385px;top:769px;width:155px;height:24px">Phone</div>
<div class="abs field" style="left:221px;top:805px;width:325px;height:52px">Message</div>
<div class="abs submit">SUBMIT</div>

<!-- footer -->
<footer class="abs footer"></footer>
<div class="abs f-brand">
  <div class="brand-box"></div>
  <div><div class="brand-name">BRISK HARBOR</div><div class="brand-tag">CLAIMS RECOVERY SERVICES</div></div>
</div>
<p class="abs f-text" style="left:63px;top:1084px;width:132px">Sed ut perspiciatis unde omnis isteers accusantium doloremque laudantium, totam rem aperiam, eaque ipsa quae ab illo inventore veritatis et...</p>

<h3 class="abs f-head" style="left:239px;top:1044px">NAVIGATION</h3>
<div class="abs f-links" style="left:239px;top:1062px">Home<br>About Us</div>
<div class="abs f-links" style="left:283px;top:1062px">Services<br>Contact Us</div>

<h3 class="abs f-head" style="left:377px;top:1044px">NEWSLETTER</h3>
<p class="abs f-text" style="left:377px;top:1062px;width:158px;line-height:13.5px">Excepteur sint occaecat cupidatat non proident, sunt in culpa qui officia deserunt mollit anim enim ipsam voluptatem quia...</p>
<div class="abs nl-input">Enter your email address</div>
<div class="abs nl-btn">Sign Up</div>

<h3 class="abs f-head" style="left:586px;top:1044px">CONTACT US</h3>
<p class="abs f-text" style="left:586px;top:1066px;line-height:14.5px;white-space:nowrap">22 Harbor Row, Brisk Harbor Tower;<br>Dubai-1020</p>
<div class="abs" style="left:588px;top:1105px;display:flex;align-items:center;gap:10px;color:#fff;font-size:10.5px;white-space:nowrap">
  <svg width="11" height="11" viewBox="0 0 10 10"><path d="M1 1.5l2.4-.5 1.1 2.4-1.2 1c.6 1.2 1.4 2 2.5 2.5l1-1.2 2.4 1.1-.5 2.4C4.6 9.2.8 5.4 1 1.5z" fill="none" stroke="#fff" stroke-width=".7"/></svg>
  (900) 555-0188
</div>
<div class="abs" style="left:588px;top:1129px;display:flex;align-items:center;gap:10px;color:#fff;font-size:7.6px;white-space:nowrap">
  <svg width="11" height="8" viewBox="0 0 11 8"><rect x=".4" y=".4" width="10.2" height="7.2" fill="none" stroke="#fff" stroke-width=".7"/><path d="M.4.4l5.1 4 5.1-4" fill="none" stroke="#fff" stroke-width=".7"/></svg>
  mail@briskharbor.example
</div>

<p class="abs f-text" style="left:63px;top:1175px;white-space:nowrap">Copyrights©briskharbor.2016 | Allrights Reserved.</p>
<p class="abs f-text" style="left:579px;top:1175px;white-space:nowrap">Connect With Us:</p>
<span class="abs social" style="left:645px"></span>
<span class="abs social" style="left:667px"></span>
<span class="abs social" style="left:689px"></span>

</body>
</html>
```